Business Cards Needed for Innovative Healthcare Marketing Company

We are a marketing company focused on healthcare. Our company is all about rebranding yourself renewing your image and generating results. The phoenix stands for "reborn" or "rising" which we provide new brands for our clients we take their old brands and renew it with creativity and innovation. I am looking for a business card with color dimension. I have attached an example of a card I think has the look and feel of what I am trying to accomplish. I like that the card example has black and grey font colors, I like the font placement and the small logo, I really like the use of the colors on the right those are the colors of my logo. My logo is phoenix so maybe incorporating flames similar to that design. I would like the back a solid color maybe red with an opaque version of the logo and website. As a marketing company I am always open to creative liberty!

Target Market(s)

Doctors and business professionals.

Industry/Entity Type

Marketing

Contact Information for Business Card

Valcorne Health Care Marketing
Marla Tenwick- CEO
#(512)638-2974
email-marla@valcorne.com
website- valcorne.com

Font styles to use
Sans Serif

Colors
ec1f27
f37122
ffc214
fbed22
fbf289
f04a50

Requirements
Must have
• The logo and required information
Nice to have
• icons by the information
Should not have
• child like font

```html
<!DOCTYPE html>
<html lang="en">
<head>
<meta charset="utf-8">
<title>Valcorne Health Care Marketing – Business Cards</title>
<link rel="stylesheet" href="https://fonts.googleapis.com/css2?family=Open+Sans:wght@300;400;700&display=swap">
<style>
  :root {
    --bg: #e4e5e8;
    --card-white: #ffffff;
    --card-shade: #f1f1f1;
    --red-deep: #a11c22;
    --red: #b0232a;
    --orange: #f37122;
    --orange-glow: #f68a2a;
    --orange-text: #e0621c;
    --ink: #2a2a2a;
    --ink-soft: #3c3c3c;
    --white: #ffffff;
  }
  * { box-sizing: border-box; margin: 0; padding: 0; }
  html, body { width: 1200px; height: 864px; overflow: hidden; }
  body {
    background: var(--bg);
    font-family: "Open Sans", Arial, sans-serif;
    position: relative;
  }
  .card {
    position: absolute;
    width: 560px;
    height: 320px;
    border-radius: 4px;
    overflow: hidden;
    box-shadow: 0 10px 26px rgba(0,0,0,.18);
  }

  /* Back of card */
  .card-back {
    left: 320px; top: 62px;
    background: radial-gradient(ellipse 48% 62% at 52% 45%, var(--orange-glow) 0%, var(--orange) 30%, #d94a1f 62%, var(--red-deep) 100%);
  }
  .back-brand {
    position: absolute;
    left: 0; right: 0; top: 112px;
    text-align: center;
    color: var(--white);
    font-weight: 300;
    line-height: 1.1;
  }
  .back-brand .brand-name { display: block; font-size: 56px; letter-spacing: 3px; }
  .back-brand .brand-line { display: block; font-size: 20px; letter-spacing: 1.5px; margin-top: 8px; }

  /* Front of card */
  .card-front {
    left: 320px; top: 482px;
    background: linear-gradient(120deg, var(--card-white) 40%, var(--card-shade) 100%);
  }
  .holder { position: absolute; left: 46px; top: 112px; }
  .holder-name { color: var(--orange-text); font-weight: 700; font-size: 20px; }
  .holder-role { color: var(--ink); font-size: 13px; margin-top: 2px; }

  .front-brand {
    position: absolute;
    right: 40px; top: 40px;
    display: flex; align-items: center; gap: 10px;
    color: var(--red);
    font-weight: 300;
    line-height: 1.05;
  }
  .front-brand .brand-dot {
    width: 46px; height: 46px; border-radius: 50%;
    background: var(--orange);
    flex: none;
  }
  .front-brand .brand-name { display: block; font-size: 32px; letter-spacing: 1px; }
  .front-brand .brand-line {
    display: block; font-size: 12px; letter-spacing: .8px;
    margin-top: 3px; padding-top: 3px;
    border-top: 1px solid var(--red);
  }

  .contact-list {
    position: absolute;
    left: 250px; top: 196px;
    list-style: none;
    color: var(--ink-soft);
    font-size: 14px;
  }
  .contact-list li { display: flex; align-items: center; gap: 12px; height: 22px; }
  .contact-list svg { width: 12px; height: 12px; flex: none; }

  .front-bands { position: absolute; left: 0; bottom: 0; width: 560px; height: 56px; }
</style>
</head>
<body>

  <section class="card card-back" aria-label="Card back">
    <div class="back-brand">
      <span class="brand-name">VALCORNE</span>
      <span class="brand-line">HEALTH CARE MARKETING</span>
    </div>
  </section>

  <section class="card card-front" aria-label="Card front">
    <div class="holder">
      <p class="holder-name">Marla Tenwick</p>
      <p class="holder-role">CEO</p>
    </div>

    <div class="front-brand">
      <span class="brand-dot"></span>
      <div>
        <span class="brand-name">VALCORNE</span>
        <span class="brand-line">HEALTH CARE MARKETING</span>
      </div>
    </div>

    <ul class="contact-list">
      <li>
        <svg viewBox="0 0 24 24" aria-hidden="true"><path fill="#e0621c" d="M6.6 10.8a15.1 15.1 0 0 0 6.6 6.6l2.2-2.2c.3-.3.7-.4 1-.2 1.1.4 2.3.6 3.6.6.6 0 1 .4 1 1V20c0 .6-.4 1-1 1A17 17 0 0 1 3 4c0-.6.4-1 1-1h3.5c.6 0 1 .4 1 1 0 1.3.2 2.5.6 3.6.1.3 0 .7-.2 1z"/></svg>
        (512)638-2974
      </li>
      <li>
        <svg viewBox="0 0 24 24" aria-hidden="true"><rect x="2" y="5" width="20" height="14" rx="2" fill="#e0621c"/><path d="M3 6l9 7 9-7" fill="none" stroke="#fff" stroke-width="2"/></svg>
        marla@valcorne.com
      </li>
      <li>
        <svg viewBox="0 0 24 24" aria-hidden="true"><circle cx="12" cy="12" r="10" fill="#e0621c"/><path d="M2 12h20M12 2c3 3 3 17 0 20M12 2c-3 3-3 17 0 20" fill="none" stroke="#fff" stroke-width="1.6"/></svg>
        www.valcorne.com
      </li>
    </ul>

    <svg class="front-bands" viewBox="0 0 560 56" aria-hidden="true">
      <polygon points="0,24 232,24 220,56 0,56" fill="var(--orange)"/>
      <polygon points="246,14 560,14 560,56 230,56" fill="var(--red)"/>
      <polygon points="0,44 560,44 560,56 0,56" fill="var(--red-deep)"/>
    </svg>
  </section>

</body>
</html>
```